Business Card for a New Zealand IT Startup

I need a business card for VELTA Holdings. We are a young startup based in New Zealand working in internet marketing and web development. The design should have some element connected to New Zealand, such as wave, koru or silver fern, just don't use a kiwi bird.

```html
<!DOCTYPE html>
<html lang="en">
<head>
<meta charset="utf-8">
<title>VELTA Holdings – Business Card</title>
<link href="https://fonts.googleapis.com/css2?family=Open+Sans:wght@400;600;700&display=swap" rel="stylesheet">
<style>
  :root {
    --backdrop: #3b3c3f;
    --card: #1e1f23;
    --foil: #8d8f93;
    --brand-blue: #1d86d0;
    --accent-orange: #ee6a22;
    --ink-light: #eef0f2;
    --ink-muted: #c9ccd0;
  }
  * { margin: 0; padding: 0; box-sizing: border-box; }
  html, body { width: 799px; height: 1200px; overflow: hidden; }
  body {
    background: var(--backdrop);
    font-family: "Open Sans", Arial, sans-serif;
    position: relative;
  }
  .card {
    position: absolute;
    left: 80px;
    width: 640px;
    height: 366px;
    background: var(--card);
    border-radius: 30px;
    box-shadow: 0 12px 30px rgba(0,0,0,0.45);
  }
  .card--front { top: 117px; }
  .card--back { top: 717px; }

  .brand {
    display: flex;
    align-items: center;
    gap: 12px;
    font-weight: 700;
    white-space: nowrap;
  }
  .brand__dot {
    width: 18px; height: 18px;
    border-radius: 50%;
    flex: none;
  }
  .card--front .brand {
    position: absolute;
    left: 0; right: 0; top: 0; bottom: 0;
    justify-content: center;
    color: var(--foil);
    font-size: 50px;
    letter-spacing: 1px;
  }
  .card--front .brand__dot { background: var(--foil); width: 22px; height: 22px; }

  .card--back .brand {
    position: absolute;
    left: 40px;
    top: 150px;
    color: var(--brand-blue);
    font-size: 30px;
  }
  .card--back .brand__dot { background: var(--brand-blue); width: 14px; height: 14px; }

  .contact {
    position: absolute;
    left: 350px;
    top: 118px;
    color: var(--ink-light);
  }
  .contact__name {
    color: var(--brand-blue);
    font-weight: 700;
    font-size: 21px;
    line-height: 1.1;
  }
  .contact__role {
    font-size: 12px;
    color: var(--ink-muted);
    margin-top: 2px;
  }
  .contact__address {
    font-size: 13.5px;
    line-height: 1.4;
    margin-top: 14px;
  }
  .contact__list {
    list-style: none;
    margin-top: 8px;
    font-size: 14.5px;
  }
  .contact__item {
    display: flex;
    align-items: center;
    gap: 10px;
    line-height: 1.55;
  }
  .contact__icon { width: 13px; height: 13px; flex: none; }
  .contact__icon path, .contact__icon circle, .contact__icon rect { fill: var(--accent-orange); }
  .icon-stroke { fill: none !important; stroke: var(--card); stroke-width: 1.2; }
</style>
</head>
<body>

  <section class="card card--front">
    <div class="brand"><span class="brand__dot"></span>VELTA Holdings</div>
  </section>

  <section class="card card--back">
    <div class="brand"><span class="brand__dot"></span>VELTA Holdings</div>

    <div class="contact">
      <p class="contact__name">Aria Tane Walker</p>
      <p class="contact__role">Managing Director</p>
      <p class="contact__address">58 Harbour Lane, Kauri Bay,<br>Auckland, NZ 1010</p>
      <ul class="contact__list">
        <li class="contact__item">
          <svg class="contact__icon" viewBox="0 0 16 16" aria-hidden="true">
            <path d="M3 2h3l1.5 3.5-2 1.3a8 8 0 0 0 3.7 3.7l1.3-2L14 10v3a1 1 0 0 1-1 1A11 11 0 0 1 2 3a1 1 0 0 1 1-1z"/>
          </svg>
          <span>021-4455-789</span>
        </li>
        <li class="contact__item">
          <svg class="contact__icon" viewBox="0 0 16 16" aria-hidden="true">
            <rect x="1" y="3" width="14" height="10" rx="1"/>
            <path class="icon-stroke" d="M1.5 3.5 8 9l6.5-5.5"/>
          </svg>
          <span>hello@veltaholdings.com</span>
        </li>
        <li class="contact__item">
          <svg class="contact__icon" viewBox="0 0 16 16" aria-hidden="true">
            <circle cx="8" cy="8" r="7"/>
            <path class="icon-stroke" d="M1 8h14M8 1c-3 3.5-3 10.5 0 14M8 1c3 3.5 3 10.5 0 14"/>
          </svg>
          <span>www.veltaholdings.com</span>
        </li>
      </ul>
    </div>
  </section>

</body>
</html>
```